Design for a real estate wev portal

Contents and features of the site
---------------------------------
Website in 5 languages: French, Dutch, English, German, Spanish.
English name of the site: Harbor Nest Place
Main purpose of the site:
- allow people to rent their house/ appartment for flatsharing purposes.
- help people wanting to find a room in flatsharing
- help people to find additional roommates for their flatsharing
Key interaction sequence:
1. I create a "group" of people who have common interest/hobbies
2. People who have the same interests/hobbies join my group
3. I look for a house/appartment to host my group
Website structure will be the following:
- Home
- Groups
-- Look for a group
--- Join a group
-- Create a group
- Properties
-- Look for a house/appartement
-- Apply
- Sales conditions
- Contact
- My account
-- My profile
-- My groups OR my properties
Your mission
------------
The client has no graphical guidelines, simply a logo (see attached).
We need a (responsive compliant) design for the following pages (we expect PSD's from you. No HTML nor CSS):
1. homepage (see example and wireframe attached)
2. properties search result list (see wireframe attached)
3. "detailed" form for properties
4. groups search result list
5. "detailed" form for groups
6. my account page
FOR THE COMPETITION step we only expect from you the design of first 2 screens.
Based on that, we will select the designer who will win the project, and will have to design the 4 remaining screens.
Target Market(s)
B2C
Industry/Entity Type
Real Estate
Number of Pages Required
5+ page
Look and feel
Each slider illustrates characteristics of the customer's brand and the style your logo design should communicate.

```html
<!DOCTYPE html>
<html lang="en">
<head>
<meta charset="utf-8">
<title>Harbor Nest Place</title>
<link href="https://fonts.googleapis.com/css2?family=Open+Sans:wght@400;600;700&family=Montserrat:wght@500;600;700&display=swap" rel="stylesheet">
<style>
:root{
  --teal:#1899ad;
  --green:#6cbf47;
  --ink:#2b3036;
  --text:#555b61;
  --muted:#8a9096;
  --line:#dfe2e5;
  --soft:#f1f2f3;
  --white:#ffffff;
}
*{box-sizing:border-box;margin:0;padding:0}
html,body{width:1200px;height:2727px;overflow:hidden;background:var(--white)}
body{position:relative;font-family:"Open Sans",Arial,sans-serif;color:var(--text);font-size:13px}
.abs{position:absolute}
h2,h3,h4{font-family:"Montserrat","Open Sans",sans-serif;color:var(--ink)}

/* header */
.site-header{position:absolute;left:0;top:0;width:1200px;height:105px;background:var(--white)}
.menu-toggle{left:100px;top:44px;display:flex;align-items:center;gap:14px;font-size:13px;color:var(--ink)}
.brand{left:470px;top:22px;width:260px;text-align:center;display:flex;align-items:center;justify-content:center;gap:10px}
.brand-dot{width:16px;height:16px;border-radius:50%;background:var(--green)}
.brand-name{font-family:"Montserrat",sans-serif;font-weight:700;font-size:25px;line-height:28px;color:var(--ink);width:170px;text-align:left}
.btn{display:inline-flex;align-items:center;justify-content:center;color:var(--white);font-size:12.5px;border-radius:4px}
.btn-login{left:774px;top:37px;width:124px;height:34px;background:var(--teal);border-radius:17px}
.nav-account{left:924px;top:45px;font-size:12.5px;color:var(--ink)}
.nav-lang{left:1022px;top:45px;font-size:12.5px;color:var(--ink);display:flex;align-items:center;gap:6px}
.flag{width:16px;height:11px;background:#2d4a8c;border:1px solid #c8102e}

/* hero */
.hero{left:0;top:105px;width:1200px;height:513px;background:linear-gradient(180deg,#f2b87a 0%,#b9734a 35%,#5a4a3b 55%,#2f8c95 75%,#1e6f7a 100%)}
.hero-title{left:0;top:325px;width:1200px;text-align:center;font-family:"Montserrat",sans-serif;font-weight:700;font-size:46px;color:var(--white);letter-spacing:.5px}
.hero-sub{left:0;top:393px;width:1200px;text-align:center;font-size:21px;color:var(--white);letter-spacing:.3px}
.hero-dots{left:574px;top:591px;display:flex;gap:8px}
.hero-dots span{width:8px;height:8px;border-radius:50%;background:rgba(255,255,255,.6)}
.hero-dots span.on{background:var(--green)}

/* section titles */
.section-title{font-size:22px;font-weight:600}
.pager{display:flex;gap:4px}
.pager span{width:23px;height:23px;border:1px solid var(--line);display:flex;align-items:center;justify-content:center;border-radius:3px}

/* tile cards */
.tile{width:229px;height:224px;border:1px solid var(--line)}
.tile-img{height:163px}
.tile-text{padding:10px 14px;font-size:13.5px;line-height:21px;color:var(--ink);height:59px;display:flex;align-items:center}

/* spotlight */
.spot{width:478px;height:157px;border:1px solid var(--line)}
.spot-img{position:absolute;left:8px;top:10px;width:170px;height:135px}
.spot-body{position:absolute;left:204px;top:20px;width:260px;font-size:11.5px;line-height:23px}
.spot-body h4{font-size:12.5px;font-weight:700;margin-bottom:2px;letter-spacing:.3px}
.hl-teal{color:var(--teal)}
.hl-green{color:var(--green)}
.btn-green{background:var(--green);height:36px;border-radius:3px}

/* key selling band */
.band{top:1509px;height:193px;width:600px;padding:42px 0 0 100px;color:var(--white)}
.band h3{color:var(--white);font-size:19px;font-weight:600;margin-bottom:12px}
.band p{font-size:12.5px;line-height:23px;width:410px}
.band-teal{left:0;background:var(--teal)}
.band-green{left:600px;background:var(--green);padding-left:98px}

/* faq */
.faq-title{left:0;top:1776px;width:1200px;text-align:center;font-size:24px;font-weight:600}
.faq-item{left:160px;width:880px;height:50px;border:1px solid var(--line);padding:0 20px;display:flex;align-items:center;justify-content:space-between;font-size:12.5px;font-weight:600;color:var(--ink)}
.faq-answer{left:184px;top:1905px;width:850px;font-size:11.5px;line-height:21px;color:var(--text)}
.faq-answer a{color:var(--green);text-decoration:none}

/* features */
.feature h3{font-size:22px;font-weight:600;margin-bottom:10px}
.feature p{font-size:11.5px;line-height:21px;width:390px}

/* footer */
.footer-rule{left:0;top:2440px;width:1200px;height:1px;background:var(--line)}
.footer-brand{left:100px;top:2512px;display:flex;align-items:center;gap:10px}
.footer-brand .brand-name{width:165px;font-size:24px}
.footer-col h4{font-size:15.5px;font-weight:600;margin-bottom:14px}
.footer-col li{list-style:none;font-size:11.5px;line-height:23px;color:var(--text)}
.contact-line{display:flex;align-items:center;gap:10px}
.socials{display:flex;gap:9px;margin-top:14px}
.socials span{width:33px;height:33px;border-radius:50%}
.copyright{left:0;top:2682px;width:1200px;height:45px;background:var(--soft);text-align:center;line-height:45px;font-size:11.5px;color:var(--muted)}
</style>
</head>
<body>

<header class="site-header">
  <div class="abs menu-toggle">
    <svg width="14" height="12" viewBox="0 0 14 12"><rect y="0" width="10" height="2" fill="#6cbf47"/><rect y="5" width="14" height="2" fill="#2b3036"/><rect y="10" width="10" height="2" fill="#6cbf47"/></svg>
    Menu
  </div>
  <div class="abs brand"><span class="brand-dot"></span><span class="brand-name">Harbor Nest Place</span></div>
  <a class="abs btn btn-login">Create / log in</a>
  <div class="abs nav-account">My Account ⌄</div>
  <div class="abs nav-lang"><span class="flag"></span>English ⌄</div>
</header>

<section>
  <div class="abs hero" role="img" aria-label="Resort house with a pool and palm trees at sunset"></div>
  <h1 class="abs hero-title">HARBOR NEST PLACE</h1>
  <p class="abs hero-sub">PEOPLE TO RENT THEIR HOUSE/ APPARTMENT FOR FLATSHARING PURPOSES</p>
  <div class="abs hero-dots"><span class="on"></span><span></span><span></span><span></span></div>
</section>

<!-- entry paths -->
<h2 class="abs section-title" style="left:100px;top:672px">Searching for accommodation</h2>
<div class="abs pager" style="left:527px;top:676px"><span>‹</span><span>›</span></div>
<h2 class="abs section-title" style="left:624px;top:672px">I have a house for rent</h2>
<div class="abs pager" style="left:1051px;top:676px"><span>‹</span><span>›</span></div>

<div class="abs tile" style="left:100px;top:731px"><div class="tile-img" role="img" aria-label="People walking in a busy street" style="background:linear-gradient(135deg,#6a7480,#3c4650 60%,#a08a70)"></div><div class="tile-text">I want to rent a room right now!</div></div>
<div class="abs tile" style="left:349px;top:731px"><div class="tile-img" role="img" aria-label="Group of smiling young women" style="background:linear-gradient(135deg,#cfcfcf,#6e5646 55%,#2b2624)"></div><div class="tile-text">I want to join a group</div></div>
<div class="abs tile" style="left:624px;top:731px"><div class="tile-img" role="img" aria-label="Modern house lit up at dusk" style="background:linear-gradient(180deg,#1f4d8a,#2a3446 55%,#d49a45)"></div><div class="tile-text">I want to advertise!</div></div>
<div class="abs tile" style="left:874px;top:731px"><div class="tile-img" role="img" aria-label="Modern villa with a lit pool" style="background:linear-gradient(180deg,#25345e,#5b6b8c 50%,#2e9bd0)"></div><div class="tile-text">Why is flatsharing interesting for me?</div></div>

<!-- spotlight -->
<h2 class="abs section-title" style="left:100px;top:1018px">Under the spotlight</h2>
<h2 class="abs section-title" style="left:624px;top:1018px">Under the spotlight</h2>

<div class="abs spot" style="left:100px;top:1073px">
  <div class="spot-img" role="img" aria-label="Friends sharing a meal" style="background:linear-gradient(135deg,#c89a6a,#6a4a34 60%,#e2d3bd)"></div>
  <div class="spot-body"><h4>A NICE GROUP</h4><div>Young workers, seeking for accomodation downtown</div><div><span class="hl-teal">Average age:</span> 35</div><div>Men and women welcome</div></div>
</div>
<div class="abs spot" style="left:100px;top:1244px">
  <div class="spot-img" role="img" aria-label="Group of friends taking a photo together" style="background:linear-gradient(135deg,#e5a13a,#b04a3a 55%,#4a8aa8)"></div>
  <div class="spot-body"><h4>A NICE GROUP</h4><div>Young workers, seeking for accomodation downtown</div><div><span class="hl-teal">Average age:</span> 35</div><div>Men and women welcome</div></div>
</div>
<div class="abs spot" style="left:624px;top:1073px">
  <div class="spot-img" role="img" aria-label="White modern house with palm trees" style="background:linear-gradient(180deg,#6fa6d8,#e8ecef 55%,#5a7a58)"></div>
  <div class="spot-body"><h4>2 BHK HOUSE</h4><div>Town : <span class="hl-green">City name</span></div><div>Rent per month : <span class="hl-green">$650,00</span></div><div>Availability : <span class="hl-green">Now!</span></div></div>
</div>
<div class="abs spot" style="left:624px;top:1244px">
  <div class="spot-img" role="img" aria-label="White apartment building" style="background:linear-gradient(180deg,#4a8fd6,#dfe6ec 55%,#6aa43a)"></div>
  <div class="spot-body"><h4>APPARTMENT</h4><div>Town : <span class="hl-green">City name</span></div><div>Rent per month : <span class="hl-green">$650,00</span></div><div>Availability : <span class="hl-green">Now!</span></div></div>
</div>

<a class="abs btn btn-green" style="left:442px;top:1418px;width:136px">See more groups</a>
<a class="abs btn btn-green" style="left:967px;top:1418px;width:135px">See more Houses</a>

<!-- key selling points -->
<div class="abs band band-teal"><h3>Key Selling Points For The Roommates</h3><p>Consectetuer adipiscing elit, sed diam nonummy nibh euismod tincidunt ut laoreet dolore magna aliquam erat volutpat. Ut wisi enim ad minim veniam, quis laoreet dolore magna...</p></div>
<div class="abs band band-green"><h3>Key Selling Points For The Owners</h3><p>Consectetuer adipiscing elit, sed diam nonummy nibh euismod tincidunt ut laoreet dolore magna aliquam erat volutpat. Ut wisi enim ad minim veniam, quis laoreet dolore magna...</p></div>

<!-- faq -->
<h2 class="abs faq-title">Everything You Need To Know About Flatsharing</h2>
<div class="abs faq-item" style="top:1838px">Consectetuer adipiscing elit, sed diam nonummy nibh euismod tincidunt<span>›</span></div>
<p class="abs faq-answer">Consectetuer adipiscing elit, sed diam nonummy nibh euismod tincidunt ut laoreet dolore magna aliquam erat volutpat. Ut wisi enim ad minim veniam, quis nostrud exerci tation ullamcorper suscipit lobortis nisl ut aliquip ex ea commodo consequa... <a>[ Read more ]</a></p>
<div class="abs faq-item" style="top:1971px">Consectetuer adipiscing elit, sed diam nonummy nibh euismod tincidunt ut laoreet dolore magna aliquam erat volutpat.<span>⌄</span></div>
<div class="abs faq-item" style="top:2025px">Consectetuer adipiscing elit, sed diam nonummy nibh euismod tincidunt ut laoreet dolore<span>⌄</span></div>
<div class="abs faq-item" style="top:2080px">Consectetuer adipiscing elit, sed diam nonummy nibh euismod tincidunt<span>⌄</span></div>
<a class="abs btn btn-green" style="left:905px;top:2155px;width:135px">All Questions</a>

<!-- features -->
<svg class="abs" style="left:130px;top:2262px" width="46" height="46" viewBox="0 0 46 46"><circle cx="18" cy="18" r="13" fill="none" stroke="#6cbf47" stroke-width="4"/><line x1="28" y1="28" x2="43" y2="43" stroke="#6cbf47" stroke-width="6" stroke-linecap="round"/></svg>
<div class="abs feature" style="left:190px;top:2262px"><h3>Pre-Defined Searches</h3><p>Consectetuer adipiscing elit, sed diam nonummy nibh euismod tincidunt ut laoreet dolore magna aliquam erat volutpat. Ut wisi enim ad minim veniam, quis nostrud exerci tation ullamcorper suscipit...</p></div>
<svg class="abs" style="left:636px;top:2262px" width="46" height="46" viewBox="0 0 46 46"><line x1="8" y1="40" x2="36" y2="12" stroke="#6cbf47" stroke-width="6" stroke-linecap="round"/><line x1="10" y1="10" x2="40" y2="40" stroke="#6cbf47" stroke-width="6" stroke-linecap="round"/><rect x="4" y="4" width="14" height="10" fill="#6cbf47" transform="rotate(45 11 9)"/></svg>
<div class="abs feature" style="left:704px;top:2262px"><h3>Tools and Informations</h3><p>Consectetuer adipiscing elit, sed diam nonummy nibh euismod tincidunt ut laoreet dolore magna aliquam erat volutpat. Ut wisi enim ad minim veniam, quis nostrud exerci tation ullamcorper suscipit...</p></div>

<!-- footer -->
<div class="abs footer-rule"></div>
<div class="abs footer-brand"><span class="brand-dot"></span><span class="brand-name">Harbor Nest Place</span></div>

<div class="abs footer-col" style="left:338px;top:2490px">
  <h4>Harbor Nest Place</h4>
  <ul>
    <li>120 Street name, City name,</li>
    <li>Country name : 6523333</li>
    <li class="contact-line" style="margin-top:6px"><svg width="11" height="11" viewBox="0 0 12 12"><path d="M2 1l3 0 1 3-2 1c1 2 2 3 3 3l1-2 3 1 0 3c-6 0-10-4-9-9z" fill="#1899ad"/></svg>( 0150 ) 555 014</li>
    <li class="contact-line"><svg width="12" height="9" viewBox="0 0 12 9"><rect width="12" height="9" fill="#1899ad"/><path d="M0 0l6 5 6-5" fill="none" stroke="#fff"/></svg>hello@harbornestplace.example</li>
  </ul>
</div>
<div class="abs footer-col" style="left:605px;top:2490px">
  <h4>Welcome</h4>
  <ul><li>Home</li><li>About Us</li><li>Services</li><li>Property</li><li>Faq's</li></ul>
</div>
<div class="abs footer-col" style="left:764px;top:2490px">
  <h4>Information</h4>
  <ul><li>Terms &amp; Conditions</li><li>Privacy policy</li><li>Disclaimer</li><li>Contact us.</li><li>Sitemap</li></ul>
</div>
<div class="abs footer-col" style="left:931px;top:2490px">
  <h4>Social media</h4>
  <ul><li>Connect with our social network</li></ul>
  <div class="socials"><span style="background:#2c5aa8"></span><span style="background:#3aa7e0"></span><span style="background:#d8322b"></span><span style="background:#1f78a8"></span></div>
</div>

<div class="abs copyright">Copyright © Harbor Nest Place. 2016.All rights reserved.</div>

</body>
</html>
```